COMPANY NAME: Bright Harbor Ventures: Task Description: We are a new UK based business with global rea

Target Market

- Personal and professional development – 30-55 age group, corporate leaders, Eastern European and Asian markets
- On-assignment projects – Corporate market – Eastern European and Asian Markets
- Property investment - 35-65 age group, Europe, USA, Australia

What we need

We need logos and brand design for a suite of web platforms (website, twitter and Facebook profile). We would like to have a cohesive and consistent look across all of our online platforms. The design suite must therefore include social media logos, backgrounds and headers. Specifically we are looking for:

a. Facebook header/page design: likely to have a more youthful look

b. Website: Header, background and layout that is responsive to devices, iPhone primarily, then tablet, then PC (we have purchased a website building package from SiteKettle so if you are familiar with one of their themes, it would be great to have a design that fits with a theme you would recommend); Design should be able to accommodate a place to position video in the medium term but an image in the short term.

c. LinkedIn: header/logo; more corporate look

d. Twitter: background/logo

e. Powerpoint template: background and logo - simple and soft background not busy

f. Electronic Newsletter: logo, header and sidebar; simple and soft background not busy

h. Business card: sophisticated and simple

Colors

We have in mind a preference for colors from the purple family, maybe lavender, so as to appeal to all genders and age groups. Though we are happy to go with a recommendation if you think otherwise.

We would like a look that is professional, airy, bright, fresh, futuristic, insightful, friendly.

Ethos of the brand

- experiencing opportunity and being fulfilled in a changing world
- services are facilitated through insights
- support provided through our product, services and tailored approach to coaching/partnerships (which includes private client match-making)
- we are service providers and passionate about quality and modern leadership skills at all stages in life.

The company name is "Bright Harbor Ventures” - our main message is helping people move to the next level - through investments, personal and professional growth.

Some of our messaging

1. International Leadership in a new world.

2. New technology;

3. Informed;

4. Positively Influential

5. Making a difference;

6. Empowered;

7. Risk free investments;

8. Commercial opportunity;

9. Fulfilled living;

10. Carefree and Fun Living;

11. Progression;

12. Open-minded

13. Energy/dynamic

The Business:
The business is to move people very quickly out of situations that hold them back. the situations could be their own personal situations; their career; their jobs; their teams; their ideas; their finances; their financial opportunities. Remove their fears and give them the strategies to take action. The team are international and have 40 years experience between them in this area.

We do want to come across modern and dynamic, customer outcome focussed, building long-term relationships; international.
Updates

Project Deadline Extended
Reason: We have not found the right designs - we are not just looking for a website design but also images and logos. Most images we can see in the designs are stock images - very standard. We need an image which will be the face of the company, like the shop front window. This main image will be used on social media (top image) and also the home page of the website.

Target Market(s)

30-55 years
Eastern Europe; UK; Asia; Africa; Middle East
Personal, Professional, Corporate, and Financial Growth

Industry/Entity Type

Business Service

Contact Information for Business Card

Simple and stylish
the 3 areas of the business on the reverse -

International look - Offices in UK and San Francisco

Company name
web address www.brightharborventure.com
email director@brightharborventure.com
Facebook bright harbor venture
LinkedIn Bright Harbor Venture
Twitter Bright Harbor Venture
Telephone: +44 (0) 768 213 5597

Logo Text

Something that symbolises unlimited growth - probably not text - could use the word INSIGHT in some way

Number of Pages Required

1 page

Colors
e4daeb
f3f1f8
ffffff

Requirements
Must have
• social media symbols and address
• company name
• Melanie Thorpe
• Director
• Telephone +44 (0) 768 213 5597
• Website name www.brightharborventure.co.uk
• Reverse of Card:
• Discreet, Fast, Bright Harbor Consultancy
• Corporate, Professional, Personal & Property Investment
Nice to have
• not too angular; soft lines; not too cluttered (possibly social media on the reverse and just logo, name, number on the front?
Should not have
• too busy

```html
<!DOCTYPE html>
<html lang="en">
<head>
<meta charset="utf-8">
<title>Bright Harbor Venture</title>
<link rel="stylesheet" href="https://fonts.googleapis.com/css2?family=Oswald:wght@400;500&family=Roboto+Condensed:wght@400&family=Roboto:ital,wght@0,300;0,400;0,500;1,400&display=swap">
<style>
:root{
  --blue:#2b7bc5;
  --blue-deep:#1f64a8;
  --blue-bar:rgba(28,98,170,.9);
  --footer:#3374b9;
  --footer-dark:#2d2d2d;
  --ink:#2b2b2b;
  --muted:#666;
  --light:#f4f4f4;
  --white:#fff;
  --accent:#2a8fd6;
}
*{margin:0;padding:0;box-sizing:border-box}
html,body{width:1200px;height:2590px;overflow:hidden}
body{font-family:"Roboto",Arial,sans-serif;color:var(--ink);background:var(--white);position:relative}
a{color:inherit;text-decoration:none}

/* hero */
.hero{position:absolute;left:0;top:0;width:1200px;height:605px;overflow:hidden}
.hero-photo{position:absolute;inset:0;
  background:
    radial-gradient(ellipse 360px 260px at 520px 200px,rgba(210,225,240,.55),rgba(210,225,240,0) 70%),
    radial-gradient(ellipse 500px 200px at 900px 330px,rgba(120,150,185,.35),rgba(120,150,185,0) 70%),
    linear-gradient(180deg,#56759a 0%,#3a5679 30%,#26405f 55%,#1a2c44 75%,#0f1a29 100%)}
.topbar{position:absolute;left:0;top:0;width:1200px;height:86px;background:var(--blue-bar)}
.brand{position:absolute;left:98px;top:26px;font-family:"Oswald",sans-serif;font-weight:500;font-size:27px;color:var(--white);letter-spacing:.5px}
.nav{position:absolute;right:102px;top:36px;display:flex;gap:29px;font-family:"Roboto Condensed",sans-serif;font-size:13px;color:var(--white);text-transform:uppercase}
.hero-title{position:absolute;left:98px;top:244px;font-family:"Oswald",sans-serif;font-weight:400;font-size:36px;color:var(--white)}
.hero-text{position:absolute;left:98px;top:304px;width:360px;font-size:13.5px;line-height:21px;color:var(--white)}
.dots{position:absolute;left:98px;top:388px;display:flex;gap:7px}
.dots span{width:15px;height:15px;border-radius:50%;border:1.5px solid var(--white)}
.dots span.on{background:var(--white)}

/* services */
.services{position:absolute;left:0;top:605px;width:1200px;height:509px;background:var(--light)}
.section-title{font-family:"Oswald",sans-serif;font-weight:400;font-size:28px;color:var(--ink)}
.services .section-title{position:absolute;top:40px;width:100%;text-align:center}
.service{position:absolute;top:108px;width:311px}
.service-photo{width:311px;height:183px}
.photo-consult{background:linear-gradient(120deg,#e9eef4 0%,#c7d6e6 35%,#4f6f94 65%,#22364f 100%)}
.photo-assign{background:linear-gradient(180deg,#d9e2ea 0%,#c2d2df 40%,#7fa3c0 65%,#e1e6ea 100%)}
.photo-property{background:linear-gradient(180deg,#8fb8dd 0%,#c9d6e0 35%,#9aa7b5 55%,#6e9a52 80%,#4f7c38 100%)}
.service h3{margin-top:18px;font-family:"Roboto",sans-serif;font-weight:400;font-size:19px;text-transform:uppercase;color:var(--ink)}
.service ul{list-style:none;margin-top:8px}
.service li{font-size:12.5px;color:var(--muted);line-height:21.5px;display:flex;align-items:center;gap:8px}
.service li::before{content:"";width:9px;height:9px;border-radius:50%;background:#555}
.btn-outline{display:inline-block;margin-top:13px;padding:6px 11px;border:1px solid #999;background:var(--white);font-size:12.5px;color:var(--ink)}

/* welcome */
.welcome{position:absolute;left:0;top:1114px;width:1200px;height:475px;background:linear-gradient(180deg,var(--blue) 0%,var(--blue-deep) 100%)}
.video{position:absolute;left:98px;top:88px;width:482px;height:300px;border:4px solid var(--white);
  background:
    radial-gradient(ellipse 160px 140px at 70px 60px,rgba(240,245,235,.75),rgba(240,245,235,0) 75%),
    linear-gradient(135deg,#a7c7c9 0%,#6e9bb0 40%,#3e6a8c 70%,#2c4a68 100%)}
.play{position:absolute;left:50%;top:50%;transform:translate(-50%,-50%)}
.welcome h2{position:absolute;left:611px;top:102px;font-family:"Oswald",sans-serif;font-weight:500;font-size:31px;color:var(--white)}
.welcome p{position:absolute;left:611px;width:485px;font-size:11.3px;line-height:21.5px;color:var(--white)}
.btn-light{position:absolute;left:611px;top:336px;width:123px;height:38px;border:1.5px solid var(--white);color:var(--white);font-family:"Roboto Condensed",sans-serif;font-size:12.5px;display:flex;align-items:center;justify-content:center;gap:6px}

/* blog */
.blog{position:absolute;left:0;top:1589px;width:1200px;height:354px;background:var(--white)}
.blog .section-title{position:absolute;left:98px;top:50px}
.arrows{position:absolute;left:1066px;top:60px;display:flex;gap:12px}
.post{position:absolute;top:117px;display:flex;gap:26px}
.post-photo{width:187px;height:163px}
.photo-laptop{background:linear-gradient(135deg,#8e6f86 0%,#d9d4dc 35%,#eef0f3 60%,#b7c6d8 100%)}
.photo-desk{background:linear-gradient(135deg,#d8c4a8 0%,#f3eee6 40%,#e6e2dc 65%,#b59f86 100%)}
.post-body{width:270px}
.post h4{font-weight:400;font-size:15.5px;line-height:20px;color:var(--ink)}
.post time{display:block;margin-top:10px;font-style:italic;font-size:13px;color:var(--accent)}
.post p{margin-top:10px;font-size:11.5px;line-height:19px;color:var(--muted)}
.post .more{display:block;margin-top:14px;font-size:12.5px;color:var(--ink)}

/* testimonials */
.testimonials{position:absolute;left:0;top:1943px;width:1200px;height:340px;color:var(--white);text-align:center;
  background:linear-gradient(180deg,#1a2130 0%,#1c2739 45%,#2b3a50 68%,#1b2535 80%,#0d121b 100%)}
.testimonials .section-title{position:absolute;top:64px;width:100%;color:var(--white)}
.quote{position:absolute;left:212px;top:130px;width:780px;font-size:12px;line-height:19px}
.quote-mark{position:absolute;left:0;top:-10px;font-family:"Oswald",sans-serif;font-size:28px}
.author{position:absolute;top:216px;width:100%;font-style:italic;font-size:17px}
.author small{font-size:12px}
.bars{position:absolute;left:553px;top:264px;display:flex;gap:6px}
.bars span{width:29px;height:3px;background:#555}
.bars span.on{background:var(--white)}

/* footer */
.footer{position:absolute;left:0;top:2283px;width:1200px;height:247px;background:var(--footer);color:var(--white)}
.footer h5{font-family:"Roboto",sans-serif;font-weight:400;font-size:15.5px;text-transform:uppercase}
.col{position:absolute;top:42px}
.col p{font-size:11.3px;line-height:21px}
.email{margin-top:12px;width:245px;height:42px;background:var(--white);color:#333;font-size:11.5px;padding:14px 14px}
.subscribe{margin-top:10px;width:102px;height:40px;background:var(--footer-dark);font-size:11.5px;display:flex;align-items:center;justify-content:center;text-transform:uppercase}
.contact{display:flex;gap:14px;font-size:12.5px;line-height:20px;margin-top:16px}
.contact svg{flex:none;margin-top:3px}
.links{list-style:none;margin-top:10px}
.links li{font-size:11.5px;line-height:22.5px}
.foot-brand{position:absolute;left:890px;top:70px;width:226px;text-align:center;font-family:"Oswald",sans-serif;font-weight:500;font-size:27px;line-height:32px;letter-spacing:.5px}
.social{position:absolute;left:936px;top:146px;display:flex;gap:6px}
.social span{width:32px;height:32px;border-radius:50%;border:1.5px solid var(--white);background:rgba(255,255,255,.12)}
.copyright{position:absolute;left:0;top:2530px;width:1200px;height:60px;background:var(--footer-dark);color:#ddd;font-size:11.5px;display:flex;align-items:center;justify-content:center}
</style>
</head>
<body>

<header class="hero">
  <div class="hero-photo" role="img" aria-label="Business people shaking hands in an office with a city skyline window"></div>
  <div class="topbar">
    <div class="brand">BRIGHT HARBOR VENTURE</div>
    <nav class="nav">
      <a>Home</a><a>About Us</a><a>Our Values</a><a>Testimonials</a><a>News Alert</a><a>Contact Us</a>
      <svg width="14" height="14" viewBox="0 0 14 14"><circle cx="5.5" cy="5.5" r="4.3" fill="none" stroke="#fff" stroke-width="2"/><line x1="8.6" y1="8.6" x2="13" y2="13" stroke="#fff" stroke-width="2.2"/></svg>
    </nav>
  </div>
  <h1 class="hero-title">BRIGHT HARBOR VENTURE</h1>
  <p class="hero-text">Lorem ipsum dolor sit amet, consectetur adipiscing<br>Sed ut perspiciatis unde sed do eiusmod<br>tempor incididunt ut labore</p>
  <div class="dots"><span class="on"></span><span></span><span></span></div>
</header>

<section class="services">
  <h2 class="section-title">OUR SERVICES</h2>
  <article class="service" style="left:98px">
    <div class="service-photo photo-consult" role="img" aria-label="Two consultants reviewing documents together"></div>
    <h3>Consultancy</h3>
    <ul><li>Professional and Personal</li><li>Next Generation Leaders (16-30)</li><li>Consultation Options</li></ul>
    <a class="btn-outline">Learn More</a>
  </article>
  <article class="service" style="left:446px">
    <div class="service-photo photo-assign" role="img" aria-label="Presenter leading a team meeting at a whiteboard"></div>
    <h3>On Assignment</h3>
    <ul><li>Team Cohesion Strategy</li><li>Go To Market Strategy</li><li>Internationalisation Strategy</li></ul>
    <a class="btn-outline">Learn More</a>
  </article>
  <article class="service" style="left:789px">
    <div class="service-photo photo-property" role="img" aria-label="Couple meeting an agent in front of a house"></div>
    <h3>Property: Private Client</h3>
    <ul><li>Promotion and cash-buyer matching</li><li>Investment: high return projects</li><li>Commercial: Hotels and Senior Housing</li></ul>
    <a class="btn-outline">Learn More</a>
  </article>
</section>

<section class="welcome">
  <div class="video" role="img" aria-label="Video still of a team working together at a laptop">
    <svg class="play" width="58" height="58" viewBox="0 0 58 58"><circle cx="29" cy="29" r="27" fill="rgba(40,40,40,.7)" stroke="#fff" stroke-width="2"/><path d="M23 17 L41 29 L23 41 Z" fill="#fff"/></svg>
  </div>
  <h2>WELCOME TO BRIGHT HARBOR VENTURE</h2>
  <p style="top:160px">If you seek an experienced and trusted partner to work with you on an assignment or simply want some strategies to move your personal or professional talents to the next level then you are in the right place. If you feel that the pace of change in business is so fast that to be an outstanding leader you should ensure you are brought up to speed regularly then you are in the right place.</p>
  <p style="top:278px">If you are hearing about the essential new leadership essentials and you are ready to hear how to adopt them into your life or business then you are at the right place.</p>
  <a class="btn-light">MORE VIDEOS <svg width="10" height="10" viewBox="0 0 10 10"><path d="M3 1 L7 5 L3 9" fill="none" stroke="#fff" stroke-width="1.8"/></svg></a>
</section>

<section class="blog">
  <h2 class="section-title">LATEST BLOG</h2>
  <div class="arrows">
    <svg width="12" height="10" viewBox="0 0 12 10"><path d="M11 5 H2 M5 1 L1 5 L5 9" fill="none" stroke="#333" stroke-width="1.5"/></svg>
    <svg width="12" height="10" viewBox="0 0 12 10"><path d="M1 5 H10 M7 1 L11 5 L7 9" fill="none" stroke="#333" stroke-width="1.5"/></svg>
  </div>
  <article class="post" style="left:98px">
    <div class="post-photo photo-laptop" role="img" aria-label="Laptop with charts and printed reports on a desk"></div>
    <div class="post-body">
      <h4>Sed ut perspiciatis unde omnis iste natus Fehler sit voluptatem</h4>
      <time>25, JUNI 2016</time>
      <p>Nulla bei diam ornare, aliquam urna vel, mmodo urna. Nam id risus ein est luctus consectetur quis eget libero. Suspendisse potenti.</p>
      <a class="more">Weiterlesen +</a>
    </div>
  </article>
  <article class="post" style="left:634px">
    <div class="post-photo photo-desk" role="img" aria-label="Businesswoman working at a bright office desk"></div>
    <div class="post-body">
      <h4>Sed ut perspiciatis unde omnis iste natus Fehler sit voluptatem</h4>
      <time>25, JUNI 2016</time>
      <p>Nulla bei diam ornare, aliquam urna vel, mmodo urna. Nam id risus ein est luctus consectetur quis eget libero. Suspendisse potenti.</p>
      <a class="more">Weiterlesen +</a>
    </div>
  </article>
</section>

<section class="testimonials" role="img" aria-label="Night city skyline over water behind testimonials">
  <h2 class="section-title">TESTIMONIALS</h2>
  <blockquote class="quote"><span class="quote-mark">“</span>Lorem ipsum dolor sit amet, consectetur adipiscing elit, sed do eiusmod tempor incididunt ut labore et dolore magna aliqua. Ut enim ad minim veniam, quis nostrud exercitation ullamco laboris nisi ut aliquip ex ea commodo consequat. Duis aute irure dolor in reprehenderit in voluptate velit esse cillum dolore eu fugiat nulla Sed ut perspiciatis unde omnis iste natus error sit voluptatem accusantium doloremque laudantium, totam rem aperiam, eaque ipsa quae ab illo inventore veritatis et quasi architecto beatae vitae</blockquote>
  <div class="author">John Doe - <small>Bright Harbor Venture</small></div>
  <div class="bars"><span class="on"></span><span></span><span></span></div>
</section>

<footer class="footer">
  <div class="col" style="left:98px;width:250px">
    <h5>Sign up for Newsletter</h5>
    <p style="margin-top:10px;width:232px">Excepteur sint occaecat cupidatat non proident, sunt in culpa qui officia deserunt</p>
    <div class="email">Enter email</div>
    <div class="subscribe">Subscription</div>
  </div>
  <div class="col" style="left:420px;width:270px">
    <h5>Contacts Us</h5>
    <div class="contact"><svg width="12" height="16" viewBox="0 0 12 16"><path d="M6 1 C2.5 1 1 3.5 1 5.8 C1 9 6 15 6 15 C6 15 11 9 11 5.8 C11 3.5 9.5 1 6 1 Z" fill="#fff"/><circle cx="6" cy="5.8" r="2" fill="#3374b9"/></svg><span>Bright Harbor Venture, New South Wales<br>Registered number 10482915</span></div>
    <div class="contact" style="margin-top:14px"><svg width="13" height="13" viewBox="0 0 13 13"><path d="M2.5 1 L5 3.5 L3.6 5.2 C4.5 7 6 8.5 7.8 9.4 L9.5 8 L12 10.5 L10.5 12 C5.5 11.5 1.5 7.5 1 2.5 Z" fill="#fff"/></svg><span>Phone: +44 (0) 768 213 5597</span></div>
    <div class="contact" style="margin-top:10px"><svg width="13" height="10" viewBox="0 0 13 10"><rect x="0.5" y="0.5" width="12" height="9" fill="#fff"/><path d="M0.5 0.5 L6.5 5.5 L12.5 0.5" fill="none" stroke="#3374b9" stroke-width="1.2"/></svg><span>director@brightharborventure.com</span></div>
  </div>
  <div class="col" style="left:729px">
    <h5>Quick Links</h5>
    <ul class="links"><li>Home</li><li>About Us</li><li>Our Values</li><li>Testimonials</li><li>Social Media</li><li>News Alert</li></ul>
  </div>
  <div class="foot-brand">BRIGHT HARBOR<br>VENTURE</div>
  <div class="social" aria-label="Social media links"><span></span><span></span><span></span><span></span></div>
</footer>
<div class="copyright">©2015 - 2016 Bright Harbor Venture, All Rights Reserved.</div>

</body>
</html>
```